Stationery Design Project for Nimbora, Chicago

Nimbora, a street parking application which helps car drivers find a street parking spot by offering an ideal path along which to look for parking. This path is calculated by our algorithm based on data (e.g. historical data, baseball games schedule, etc.). Along this path the driver will find a spot and will also save 70% of the search time. Customer we target is reg. between 21 and 45 yo.

We envision something young, fresh, bright and original. Slightly abstract maybe. It should represent the idea and elements of finding street parking in the city, e.g. car(s), parking spot, people, city, etc. (just ideas!).

Logo is attached.

Requirement:
- Business Cards (2 Sided Full Color CMYK)
- Letterhead (1 Sided Full Color CMYK)
- Envelope (1 Sided Full Color CMYK)
- Sticker (1 Sided Full Color CMYK), round with a 2inch diameter.

Reason: We're starting to get more and more designs and need more time to look into all of them. Very exciting!! Thanks to everybody!

Hi all, we're in the process of selecting our favs. Though choices!!! Really good submissions. Will keep you posted and sorry for the delay.

Target Market(s)

Car drivers and owners between 21 and 45

Industry/Entity Type

Parking

Requirements
Must have
• Sticker should be round and include company URL nimbora.com and the new logo which we will attach soon.
Should not have
• Should not be too serious or boring.

```html
<!DOCTYPE html>
<html lang="en">
<head>
<meta charset="utf-8">
<title>Nimbora — Business Card</title>
<link rel="stylesheet" href="https://fonts.googleapis.com/css2?family=Open+Sans:wght@400;600;700&display=swap">
<style>
  :root {
    --backdrop: #e6e6e6;
    --card: #ffffff;
    --ink: #1e1e1e;
    --text-grey: #5a5a5a;
    --brand-blue: #2d3b92;
    --brand-blue-light: #2a7fd4;
    --rule-navy: #1d2240;
    --photo-dark: #5c5f63;
    --photo-light: #a9abad;
  }
  * { box-sizing: border-box; margin: 0; padding: 0; }
  html, body { width: 956px; height: 1200px; overflow: hidden; }
  body {
    position: relative;
    background: var(--backdrop);
    font-family: "Open Sans", Arial, sans-serif;
  }
  .card {
    position: absolute;
    left: 88px;
    width: 798px;
    height: 456px;
    background: var(--card);
    border-radius: 28px;
    overflow: hidden;
    box-shadow: 0 4px 14px rgba(0,0,0,0.18);
  }
  .card--front { top: 100px; }
  .card--back { top: 646px; }

  .brand {
    position: absolute;
    left: 127px;
    top: 52px;
    display: flex;
    align-items: center;
    gap: 28px;
  }
  .brand__dot {
    width: 150px;
    height: 150px;
    border-radius: 50%;
    background: var(--brand-blue);
  }
  .brand__name {
    font-size: 96px;
    font-weight: 600;
    color: var(--ink);
    letter-spacing: 1px;
    line-height: 1;
  }

  .person {
    position: absolute;
    right: 431px;
    top: 272px;
    text-align: right;
    color: var(--text-grey);
    font-weight: 700;
  }
  .person__name { font-size: 24px; line-height: 32px; }
  .person__role { font-size: 18px; line-height: 26px; }

  .divider {
    position: absolute;
    left: 396px;
    top: 264px;
    width: 3px;
    height: 84px;
    background: linear-gradient(to bottom, rgba(42,127,212,0), var(--brand-blue-light), rgba(42,127,212,0));
  }

  .contact {
    position: absolute;
    left: 422px;
    top: 253px;
    list-style: none;
    color: var(--text-grey);
    font-size: 19px;
    line-height: 26.5px;
  }
  .contact__key { font-weight: 700; }

  .rule {
    position: absolute;
    left: 0;
    top: 390px;
    width: 100%;
    height: 3px;
    background: var(--rule-navy);
  }
  .address-band {
    position: absolute;
    left: 0;
    top: 400px;
    width: 100%;
    height: 56px;
    background: var(--brand-blue);
    color: #ffffff;
    font-size: 19px;
    line-height: 52px;
    text-align: center;
  }

  .street-photo {
    position: absolute;
    left: 0;
    top: 247px;
    width: 100%;
    height: 209px;
    background: linear-gradient(100deg, var(--photo-light) 0%, var(--photo-dark) 45%, #7d7f83 100%);
  }
</style>
</head>
<body>
  <section class="card card--front">
    <div class="brand">
      <div class="brand__dot"></div>
      <div class="brand__name">Nimbora</div>
    </div>

    <div class="person">
      <p class="person__name">Your Name</p>
      <p class="person__role">Designation</p>
    </div>

    <div class="divider"></div>

    <ul class="contact">
      <li><span class="contact__key">p</span> : 123-456-7890</li>
      <li><span class="contact__key">c</span> : 123-456-7890</li>
      <li><span class="contact__key">e</span> : name@website.com</li>
      <li><span class="contact__key">w</span> : www.website.com</li>
    </ul>

    <div class="rule"></div>
    <div class="address-band">City Name, Street Name, State Name, Country Code</div>
  </section>

  <section class="card card--back">
    <div class="brand">
      <div class="brand__dot"></div>
      <div class="brand__name">Nimbora</div>
    </div>
    <div class="street-photo" role="img" aria-label="Overhead photo of cars parked in street parking bays beside a sidewalk"></div>
  </section>
</body>
</html>
```